Fantasy Sports Website re-Design

We need a website designed for our fantasy sports website. The website is GriddoVane.com . An example of the website layout would be like : https://www.quorbelnet.com/fantasy-sports/fantasy-sports-solutions. We like this site, because of the screenshots on 1 side and a description on the other side. This layout style will showcase the features we have on our site. Somewhere in the header there will be a video explaining what the site is. We would like the style to be black and gold. Like a casino. Attached is an example logo to give the style we want.

Target Market(s)

fantasy sports

Number of Pages Required

3 page

Colors
fecb35
000000

Requirements
Must have
• mockups of index page
Nice to have
• mockups of sub pages

```html
<!DOCTYPE html>
<html lang="en">
<head>
<meta charset="utf-8">
<title>GriddoVane.com — One-Day Fantasy Sports</title>
<link href="https://fonts.googleapis.com/css2?family=Roboto:wght@400;500;700&family=Open+Sans:wght@400;600&display=swap" rel="stylesheet">
<style>
:root{
  --gold:#fecb35;
  --gold-deep:#f9b21a;
  --black:#000000;
  --panel:#161616;
  --lobby-bg:#232323;
  --white:#ffffff;
  --muted:#b5b5b5;
  --line:#3a3a3a;
}
*{margin:0;padding:0;box-sizing:border-box}
html,body{width:1200px;height:2344px;overflow:hidden;background:var(--black)}
body{position:relative;font-family:"Roboto",Arial,sans-serif;color:var(--white)}
.abs{position:absolute}

/* header */
.site-header{position:absolute;left:0;top:0;width:1200px;height:147px;background:var(--black)}
.brand{position:absolute;left:109px;top:50px;font-family:"Roboto",sans-serif;font-weight:700;font-size:44px;letter-spacing:1px;color:var(--gold);line-height:1}
.auth{position:absolute;top:31px;height:30px;font-size:14px;font-weight:500;display:flex;align-items:center;justify-content:center}
.auth--signup{left:841px;width:103px;border:2px solid var(--gold);color:var(--white)}
.auth--login{left:956px;width:105px;background:var(--gold);color:var(--black)}
.main-nav{position:absolute;left:442px;top:83px;width:616px;display:flex;justify-content:space-between;font-size:15px;font-weight:500;letter-spacing:.3px}

/* hero */
.hero{position:absolute;left:0;top:147px;width:1200px;height:498px;
  background:radial-gradient(ellipse at 30% 40%,#5a4320 0%,#2c2012 45%,#140e08 100%)}
.hero__title{position:absolute;left:112px;top:122px;font-size:37px;font-weight:700;line-height:46px;text-transform:uppercase}
.hero__title span{color:var(--gold)}
.hero__lead{position:absolute;left:112px;top:222px;font-size:22px;font-weight:400}
.btn-primary{position:absolute;left:114px;top:270px;width:186px;height:50px;background:linear-gradient(var(--gold),var(--gold-deep));color:var(--black);font-size:19px;font-weight:500;display:flex;align-items:center;justify-content:center}
.video-frame{position:absolute;left:586px;top:75px;width:498px;height:312px}
.video{position:absolute;left:12px;top:12px;width:475px;height:289px;
  background:linear-gradient(160deg,#4d5a68 0%,#8a6a3a 55%,#2f4a2a 100%)}
.play{position:absolute;left:206px;top:113px}

/* featured */
.featured{position:absolute;left:0;top:645px;width:1200px;height:785px;background:var(--black)}
.section-title{position:absolute;left:0;width:1200px;text-align:center;font-size:31px;font-weight:500;text-transform:uppercase}
.featured .section-title{top:36px}
.game-grid{position:absolute;left:105px;top:97px;display:grid;grid-template-columns:repeat(3,309px);column-gap:21px;row-gap:25px}
.game-card{width:309px;height:298px;background:var(--panel);position:relative}
.game-card__photo{height:184px}
.game-card__title{position:absolute;left:26px;top:200px;font-size:20px;font-weight:500;color:var(--gold)}
.game-card__text{position:absolute;left:26px;top:230px;font-family:"Open Sans",sans-serif;font-size:12.5px;color:var(--muted)}
.game-card__btn{position:absolute;left:26px;top:253px;width:100px;height:27px;border:2px solid var(--gold);font-size:10px;font-weight:500;display:flex;align-items:center;justify-content:center}

/* lobby */
.lobby{position:absolute;left:0;top:1430px;width:1200px;height:553px;background:var(--lobby-bg)}
.lobby .section-title{top:55px;font-weight:400}
.filters{position:absolute;left:103px;top:126px;width:231px;height:349px;background:linear-gradient(var(--gold),var(--gold-deep));color:var(--black);overflow:hidden}
.filter{border-bottom:1px solid rgba(0,0,0,.25);padding:0 0 0 24px;font-size:16px;font-weight:500;height:56px;display:flex;align-items:center;gap:8px}
.filter:last-child{border-bottom:none}
.filter--open{height:181px;display:block;padding-top:28px;line-height:19px}
.filter--open ul{list-style:none;margin:12px 0 0 38px;font-family:"Open Sans",sans-serif;font-size:12.5px;line-height:23px;font-weight:400}
.tiles{position:absolute;left:348px;top:125px;display:grid;grid-template-columns:repeat(4,170px);column-gap:14px;row-gap:13px}
.tile{width:170px;height:169px;position:relative}
.tile__label{position:absolute;left:0;bottom:0;width:100%;height:40px;background:rgba(0,0,0,.72);display:flex;align-items:center;justify-content:center;font-size:14px;font-weight:500}

/* footer */
.site-footer{position:absolute;left:0;top:1983px;width:1200px;height:361px;background:var(--black)}
.footer-col{position:absolute;top:70px}
.footer-col h3{font-size:20px;font-weight:500;color:var(--gold);text-transform:uppercase;margin-bottom:14px}
.footer-col ul{list-style:none;font-size:16px;line-height:31px;color:#e6e6e6}
.footer-brand{position:absolute;left:763px;top:68px;font-size:44px;font-weight:700;color:var(--gold);letter-spacing:1px;line-height:1}
.socials{position:absolute;left:797px;top:144px;display:flex;gap:9px}
.socials span{width:41px;height:41px;border:2px solid var(--gold);border-radius:50%}
.footer-rule{position:absolute;left:103px;top:295px;width:969px;height:1px;background:var(--line)}
.copyright{position:absolute;left:0;top:319px;width:1200px;text-align:center;font-family:"Open Sans",sans-serif;font-size:12px;color:#9a9a9a}
</style>
</head>
<body>

<header class="site-header">
  <div class="brand">GRIDDO VANE</div>
  <a class="auth auth--signup">SIGN UP</a>
  <a class="auth auth--login">LOG IN</a>
  <nav class="main-nav">
    <span>FANTASY</span><span>LOBBY</span><span>STATISTICS</span><span>REFERRAL</span><span>MOBILE APP</span><span>GAME TYPES</span>
  </nav>
</header>

<section class="hero" role="img" aria-label="Blurred stadium crowd at night in warm gold tones">
  <h1 class="hero__title">The leader in one-day<br><span>fantasy sports</span></h1>
  <p class="hero__lead">It’s Fun, Exciting, Easy to play and 100% Legal!</p>
  <a class="btn-primary">VIEW GAMES</a>
  <div class="video-frame">
    <svg class="abs" width="498" height="312" viewBox="0 0 498 312" fill="none" stroke="#fecb35" stroke-width="2">
      <path d="M1 62V1H62M436 1H497V62M497 250V311H436M62 311H1V250"/>
    </svg>
    <div class="video" role="img" aria-label="Explainer video still: footballer kicking a ball in a floodlit stadium">
      <svg class="play" width="64" height="64" viewBox="0 0 64 64"><circle cx="32" cy="32" r="29" fill="none" stroke="#fff" stroke-width="5"/><path d="M25 19L46 32L25 45Z" fill="#fff"/></svg>
    </div>
  </div>
</section>

<section class="featured">
  <h2 class="section-title">Featured Games</h2>
  <div class="game-grid">
    <article class="game-card"><div class="game-card__photo" role="img" aria-label="Footballers in action under stadium lights" style="background:linear-gradient(#3c4a5c,#3d6b2c)"></div><h3 class="game-card__title">GAME TITLE</h3><p class="game-card__text">Curabitur vel mi sit amet magna malesuada</p><a class="game-card__btn">CLICK HERE</a></article>
    <article class="game-card"><div class="game-card__photo" role="img" aria-label="Show jumping rider on a horse in an arena" style="background:linear-gradient(#d9d6cf,#7a5a3a)"></div><h3 class="game-card__title">GAME TITLE</h3><p class="game-card__text">Curabitur vel mi sit amet magna malesuada</p><a class="game-card__btn">CLICK HERE</a></article>
    <article class="game-card"><div class="game-card__photo" role="img" aria-label="Basketball dropping toward the hoop" style="background:linear-gradient(135deg,#1d2c4a,#4a6fa8 60%,#0f1830)"></div><h3 class="game-card__title">GAME TITLE</h3><p class="game-card__text">Curabitur vel mi sit amet magna malesuada</p><a class="game-card__btn">CLICK HERE</a></article>
    <article class="game-card"><div class="game-card__photo" role="img" aria-label="Basketball player dunking in front of the crowd" style="background:linear-gradient(#5a4a3a,#2a2018)"></div><h3 class="game-card__title">GAME TITLE</h3><p class="game-card__text">Curabitur vel mi sit amet magna malesuada</p><a class="game-card__btn">CLICK HERE</a></article>
    <article class="game-card"><div class="game-card__photo" role="img" aria-label="Packed indoor basketball arena" style="background:radial-gradient(ellipse at 50% 30%,#c99a4a,#4a2a14 70%)"></div><h3 class="game-card__title">GAME TITLE</h3><p class="game-card__text">Curabitur vel mi sit amet magna malesuada</p><a class="game-card__btn">CLICK HERE</a></article>
    <article class="game-card"><div class="game-card__photo" role="img" aria-label="Close-up of a basketball on a dark purple background" style="background:linear-gradient(135deg,#c85a2a,#3a1a4a 55%,#1a1030)"></div><h3 class="game-card__title">GAME TITLE</h3><p class="game-card__text">Curabitur vel mi sit amet magna malesuada</p><a class="game-card__btn">CLICK HERE</a></article>
  </div>
</section>

<section class="lobby">
  <h2 class="section-title">Game Lobby</h2>
  <aside class="filters">
    <div class="filter filter--open"><span>— &nbsp;LEAGUE SELECTION</span>
      <ul><li>Etiam est nunc</li><li>Aenenatis in tristique</li><li>Eeu imperdiet ac nisl</li><li>Cum sociis</li><li>Natoque penatibus</li></ul>
    </div>
    <div class="filter">+ &nbsp;SPORT</div>
    <div class="filter">+ &nbsp;ENTRY FEE</div>
    <div class="filter">+ &nbsp;SIZE OF POO</div>
  </aside>
  <div class="tiles">
    <div class="tile" role="img" aria-label="Soccer player volleying a ball" style="background:linear-gradient(#9aa0a8,#3a3e44)"><span class="tile__label">GAME TITLE</span></div>
    <div class="tile" role="img" aria-label="Basketball players contesting a rebound" style="background:linear-gradient(#6a4a6a,#8a2a2a)"><span class="tile__label">GAME TITLE</span></div>
    <div class="tile" role="img" aria-label="Basketball going through the net" style="background:radial-gradient(circle at 55% 45%,#e07a20,#3a1a0a 70%)"><span class="tile__label">GAME TITLE</span></div>
    <div class="tile" role="img" aria-label="Soccer players' legs battling for the ball" style="background:linear-gradient(#3a5a2a,#5a8a2a)"><span class="tile__label">GAME TITLE</span></div>
    <div class="tile" role="img" aria-label="Soccer players under floodlights" style="background:linear-gradient(#3a4a6a,#2a3a2a)"><span class="tile__label">GAME TITLE</span></div>
    <div class="tile" role="img" aria-label="Golden trophy on a dark stage" style="background:radial-gradient(circle at 50% 40%,#a87a2a,#1a120a 70%)"><span class="tile__label">GAME TITLE</span></div>
    <div class="tile" role="img" aria-label="Soccer player tackling in a stadium" style="background:linear-gradient(#3a5a8a,#a85a2a)"><span class="tile__label">GAME TITLE</span></div>
    <div class="tile" role="img" aria-label="Soccer player dribbling on green grass" style="background:linear-gradient(#5a9a3a,#3a7a2a)"><span class="tile__label">GAME TITLE</span></div>
  </div>
</section>

<footer class="site-footer">
  <div class="footer-col" style="left:125px"><h3>Quick Links</h3><ul><li>My Live Games</li><li>My Upcoming Games</li><li>My History Games</li><li>My Account</li></ul></div>
  <div class="footer-col" style="left:350px"><h3>Resources</h3><ul><li>My Profile</li><li>Future Events</li><li>Withdrawal History</li><li>Transactions</li></ul></div>
  <div class="footer-col" style="left:573px"><h3>Sublinks</h3><ul><li>Game Summary</li><li>My Funds</li><li>Add Funds</li><li>Create Contest</li></ul></div>
  <div class="footer-brand">GRIDDO VANE</div>
  <div class="socials" aria-label="Social links"><span></span><span></span><span></span><span></span><span></span></div>
  <div class="footer-rule"></div>
  <p class="copyright">© 2018 Company Name &nbsp;All right reserved</p>
</footer>

</body>
</html>
```